Business Card Design - ChoiceCraft

Looking for creative, modern design, two sided for ChoiceCraft that is consistent with color and feel of website www.choicecraftpro.net.
Updates

Back of card will be used to promote products or have a quote revolving around decisions, change, leadership, innovation, creativity. Back should also have space to promote website, but optional to use the icon. Front of the card will need to use the icon and have standard place for name, job title, phone and email. We are not looking to put a mailing address or fax. Also want space to place a few words/phrase explaining what we do...such as individual growth and organizational development or tools, training, information...in addition, want the facebook icon small on the front somewhere as we are also on facebook.

Vector file uploaded of icon.

Target Market(s)

Professional coaching for individual growth and organizational development

Industry/Entity Type

Business

Requirements
Must have
• Icon...see attached.

```html
<!DOCTYPE html>
<html lang="en">
<head>
<meta charset="utf-8">
<title>ChoiceCraft Business Card</title>
<link rel="stylesheet" href="https://fonts.googleapis.com/css2?family=Arimo:wght@400;700&family=Tinos:wght@400;700&display=swap">
<style>
  :root {
    --page: #dcdee0;
    --white: #ffffff;
    --ink: #1a1a1a;
    --text: #333333;
    --navy: #1f3f8f;
    --blue: #1a73c6;
    --sky: #3fb2ea;
    --back-dark: #1b74c4;
    --back-light: #49a9e6;
    --rule: #c8c8c8;
  }
  * { box-sizing: border-box; margin: 0; padding: 0; }
  html, body {
    width: 1200px; height: 388px; overflow: hidden;
    background: var(--page);
  }
  .canvas { position: relative; width: 1200px; height: 388px; }

  .card {
    position: absolute; top: 39px; border-radius: 18px; overflow: hidden;
  }

  /* Front */
  .card-front {
    left: 41px; width: 544px; height: 310px; background: var(--white);
    font-family: "Tinos", "Times New Roman", serif; color: var(--text);
  }
  .brand-mark {
    position: absolute; left: 92px; top: 40px; width: 112px; height: 112px;
    border-radius: 50%; background: radial-gradient(circle at 40% 40%, #e4eaf2, #8fb4de 70%, var(--blue));
  }
  .brand-name {
    position: absolute; left: 0; width: 296px; top: 188px; text-align: center;
    font-weight: 700; font-size: 23px; color: var(--ink); letter-spacing: 0.2px;
  }
  .divider {
    position: absolute; left: 269px; top: 64px; width: 1px; height: 153px; background: var(--rule);
  }
  .contact-list { position: absolute; left: 282px; top: 42px; list-style: none; font-size: 14.5px; }
  .contact-list li { display: flex; align-items: center; height: 20.5px; }
  .contact-list svg { width: 11px; height: 11px; margin-right: 6px; flex: none; }
  .tagline {
    position: absolute; left: 282px; top: 152px; font-size: 14.5px; line-height: 18.5px; color: var(--text);
  }
  .front-waves { position: absolute; left: 0; top: 0; }
  .holder {
    position: absolute; left: 72px; top: 269px; color: var(--white);
    font-size: 17px; font-weight: 700;
  }
  .holder .title { font-weight: 400; font-size: 14px; }

  /* Back */
  .card-back {
    left: 623px; width: 539px; height: 305px;
    background: radial-gradient(ellipse at 55% 45%, var(--back-light), var(--back-dark) 85%);
    font-family: "Arimo", Arial, sans-serif; color: var(--white);
  }
  .quote { position: absolute; left: 38px; font-size: 13px; line-height: 22px; }
  .quote .open, .quote .close { font-family: "Tinos", serif; font-weight: 700; font-size: 22px; line-height: 0; }
  .quote .open { position: absolute; left: -16px; top: 10px; }
  .quote .close { position: relative; top: 6px; margin-left: 1px; }
  .quote .author { font-weight: 700; }
  .back-mark {
    position: absolute; left: 365px; top: 185px; width: 104px; height: 104px; border-radius: 50%;
    background: rgba(255,255,255,0.16);
  }
</style>
</head>
<body>
<main class="canvas">

  <section class="card card-front" aria-label="Card front">
    <svg class="front-waves" width="544" height="310" viewBox="0 0 544 310" aria-hidden="true">
      <defs>
        <linearGradient id="band" x1="0" y1="0" x2="1" y2="0">
          <stop offset="0" stop-color="#1a6fc2"/>
          <stop offset="1" stop-color="#42b7ec"/>
        </linearGradient>
      </defs>
      <path d="M0 236 C120 214 240 232 330 262 C410 286 480 280 544 262 L544 310 L0 310 Z" fill="var(--navy)"/>
      <path d="M0 248 C130 230 240 246 330 274 C410 296 480 290 544 274 L544 310 L0 310 Z" fill="var(--white)"/>
      <path d="M0 254 C130 238 240 256 330 282 C410 302 480 296 544 280 L544 310 L0 310 Z" fill="url(#band)"/>
    </svg>

    <div class="brand-mark" aria-hidden="true"></div>
    <div class="brand-name">ChoiceCraft</div>
    <div class="divider"></div>

    <ul class="contact-list">
      <li>
        <svg viewBox="0 0 12 12"><path d="M3 1 L5 3.5 L4 5 C5 7 6 8 7.5 8.5 L9 7.5 L11 9.5 L9.5 11 C5 10.5 1.5 7 1 2.5 Z" fill="var(--text)"/></svg>
        123-456-789
      </li>
      <li>
        <svg viewBox="0 0 12 12"><rect x="1" y="3" width="10" height="7" fill="var(--text)"/><path d="M1 3 L6 7 L11 3" stroke="#fff" fill="none"/></svg>
        info@choicecraftpro.net
      </li>
      <li>
        <svg viewBox="0 0 12 12"><circle cx="6" cy="6" r="5" fill="none" stroke="var(--text)"/><path d="M1 6 H11 M6 1 V11" stroke="var(--text)"/></svg>
        www.choicecraftpro.net
      </li>
      <li>
        <svg viewBox="0 0 12 12"><rect x="1" y="1" width="10" height="10" rx="1.5" fill="#3b5a9a"/></svg>
        /choicecraftpro
      </li>
    </ul>

    <p class="tagline">Supporting individual growth<br>and organizational development<br>or tools, training, information</p>

    <div class="holder">Your Name, <span class="title">Title</span></div>
  </section>

  <section class="card card-back" aria-label="Card back">
    <p class="quote" style="top:26px"><span class="open">&ldquo;</span>Try not to become a man of success, but rather a man of value.<span class="close">&rdquo;</span><br>- <span class="author">Alden Whitmore</span></p>
    <p class="quote" style="top:80px"><span class="open">&ldquo;</span>The only constant is change.<span class="close">&rdquo;</span><br>- <span class="author">Corin Vale</span></p>
    <p class="quote" style="top:134px"><span class="open">&ldquo;</span>We are what we repeatedly do. Excellence is not an act, it is a habit.<span class="close">&rdquo;</span><br>- <span class="author">Theon Marrick</span></p>
    <p class="quote" style="top:189px"><span class="open">&ldquo;</span>Simplicity is the ultimate sophistication.<span class="close">&rdquo;</span><br>- <span class="author">Lucan Deverell</span></p>
    <p class="quote" style="top:243px"><span class="open">&ldquo;</span>Life is not fair - get used to it.<span class="close">&rdquo;</span><br>- <span class="author">Brent Galloway</span></p>
    <div class="back-mark" aria-hidden="true"></div>
  </section>

</main>
</body>
</html>
```